Web Design Project

Desisgn a new style for the proposed website as per the attached link. The logo will remain as is, and it is likely that the colours will be as per the attached style guide.

Otherwise look and feel, icons, layout, images are within scope.

Current prosposed home page:
http://vantrelux-newsite.pagemorrowhost.com/index

Target Market(s)

Typically, large organisations from any industry such as Airlines, banks, Govt agencies.

Could be operational executives, business improvement specialists, bsuienss analysts.

```html
<!DOCTYPE html>
<html lang="en">
<head>
<meta charset="utf-8">
<title>Vantrelux – Operational Business Management</title>
<link rel="stylesheet" href="https://fonts.googleapis.com/css2?family=Open+Sans:wght@400;600;700&display=swap">
<style>
:root{
  --brand-blue:#1f6fb8;
  --nav-top:#2f7fc9;
  --nav-bottom:#1456a0;
  --ink:#333333;
  --ink-soft:#555555;
  --link:#1c5f9e;
  --orange-top:#f9ad1a;
  --orange-bottom:#ef9410;
  --footer-bg:#e6f1f9;
  --footer-bar:#d9e9f5;
  --rule:#cfd8df;
  --white:#ffffff;
}
*{box-sizing:border-box;margin:0;padding:0}
html,body{width:831px;height:1200px;overflow:hidden}
body{position:relative;background:var(--white);font-family:"Open Sans",Arial,sans-serif;color:var(--ink)}
.top-rule{position:absolute;left:0;top:0;width:831px;height:2px;background:var(--brand-blue)}
.site-header{position:absolute;left:0;top:2px;width:831px;height:111px;background:linear-gradient(#ffffff,#f2f4f6)}
.brand{position:absolute;left:34px;top:38px;display:flex;align-items:center;gap:10px}
.brand-dot{width:22px;height:22px;border-radius:50%;background:var(--brand-blue)}
.brand-name{font-size:28px;font-weight:400;color:var(--brand-blue);letter-spacing:.5px}
.search{position:absolute;left:588px;top:61px;display:flex}
.search-field{width:190px;height:22px;border:1px solid #c8ced3;border-radius:4px 0 0 4px;background:var(--white);font-size:9px;color:#999;padding:4px 9px;box-shadow:inset 0 1px 2px rgba(0,0,0,.08)}
.search-go{width:24px;height:24px;margin-top:-1px;border-radius:4px;background:var(--brand-blue);color:var(--white);font-size:9px;font-weight:700;display:flex;align-items:center;justify-content:center}
.main-nav{position:absolute;left:0;top:113px;width:831px;height:42px;background:linear-gradient(var(--nav-top),var(--nav-bottom));display:flex;align-items:center;border-bottom:2px solid #0f4c8f}
.main-nav a{color:var(--white);text-decoration:none;font-size:11.5px;letter-spacing:.3px;padding:0 0;height:18px;line-height:18px;text-align:center}
.nav-sep{width:1px;height:18px;background:rgba(255,255,255,.45)}
.hero{position:absolute;left:16px;top:162px;width:799px;height:246px;background:linear-gradient(100deg,#c9d6e2 0%,#e3eaf1 35%,#dfe6ee 55%,#b9cbe0 100%)}
.hero-card{position:absolute;left:70px;top:248px;width:326px;height:90px;background:var(--white);box-shadow:0 2px 4px rgba(0,0,0,.25);padding:12px 17px}
.hero-card h1{font-size:14.5px;font-weight:400;color:var(--link);letter-spacing:.3px}
.hero-card h1 strong{font-weight:700}
.hero-card p{font-size:8.6px;line-height:13px;color:var(--link);margin-top:4px}
.feature-band{position:absolute;left:13px;top:415px;width:803px;height:125px;border-radius:3px;background:linear-gradient(var(--orange-top),var(--orange-bottom));display:flex}
.feature{position:relative;flex:1;padding:15px 16px 0 20px}
.feature+.feature{border-left:1px dotted rgba(255,255,255,.8)}
.feature h2{font-size:12px;font-weight:600;color:var(--white);letter-spacing:.2px}
.feature p{font-size:8.6px;line-height:13px;color:#5a3a05;margin-top:4px;width:170px}
.read-more{position:absolute;left:18px;top:90px;width:165px;height:17px;border-radius:3px;background:linear-gradient(#ffffff,#e9e9e9);font-size:8.5px;color:#555;padding:2px 7px;box-shadow:0 2px 3px rgba(0,0,0,.2)}
.content{position:absolute;left:17px;top:556px;width:525px}
.content h2{font-size:14.5px;font-weight:400;color:#222;margin-bottom:8px}
.content p{font-size:8.6px;line-height:12.6px;color:var(--ink);margin-bottom:6px}
.benefits{list-style:none;margin-top:14px;padding-left:3px}
.benefits li{font-size:8.6px;color:var(--ink);margin-bottom:7.5px}
.benefits li::before{content:"* "}
.sidebar{position:absolute;left:575px;top:556px;width:237px}
.sidebar h3{font-size:14px;font-weight:400;color:#222;padding-bottom:4px;border-bottom:1px solid var(--rule)}
.video{margin-top:8px;width:237px;height:148px;background:#000;position:relative}
.video svg{position:absolute;left:0;top:0}
.news{margin-top:30px}
.news-item{display:flex;gap:10px;margin-top:17px}
.news-item+.news-item{margin-top:17px}
.news-body{width:190px}
.news-date{font-size:11px;color:#222}
.news-text{font-size:8.6px;line-height:13px;color:var(--ink);margin-top:3px}
.news-more{display:inline-block;margin-top:3px;background:#eef1f3;font-size:8.5px;color:var(--link);padding:2px 5px}
.news-more b{font-weight:700}
.site-footer{position:absolute;left:0;top:968px;width:831px;height:192px;background:var(--footer-bg)}
.footer-col{position:absolute;top:22px}
.footer-col h4{font-size:11px;font-weight:400;color:var(--link);letter-spacing:.2px;margin-bottom:11px}
.footer-col ul{list-style:none}
.footer-col li{font-size:9px;color:var(--link);margin-bottom:7.3px}
.footer-col li::before{content:"›";margin-right:6px}
.footer-bar{position:absolute;left:0;top:1160px;width:831px;height:40px;background:var(--footer-bar);border-top:1px solid #c6d9e8;font-size:8.5px;color:#12457a}
.copyright{position:absolute;left:20px;top:15px}
.legal{position:absolute;right:40px;top:15px}
</style>
</head>
<body>
<div class="top-rule"></div>

<header class="site-header">
  <div class="brand"><span class="brand-dot"></span><span class="brand-name">vantrelux</span></div>
  <div class="search"><div class="search-field">type your word</div><div class="search-go">Go</div></div>
</header>

<nav class="main-nav">
  <a style="width:118px">PRODUCTS</a><span class="nav-sep"></span>
  <a style="width:101px">SERVICES</a><span class="nav-sep"></span>
  <a style="width:111px">SOLUTIONS</a><span class="nav-sep"></span>
  <a style="width:115px">RESOURCES</a><span class="nav-sep"></span>
  <a style="width:153px">CUSTOMER STORIES</a><span class="nav-sep"></span>
  <a style="width:106px">ABOUT US</a><span class="nav-sep"></span>
  <a style="width:106px">CONTACT</a>
</nav>

<div class="hero" role="img" aria-label="Brushed-metal world map with a coloured DNA double helix"></div>
<div class="hero-card">
  <h1>DNA OF YOUR <strong>BUSINESS</strong></h1>
  <p>So that the website can achieve top position and ranking in the Internet searches and thereby increasing the scope for the website to be found by customers.</p>
</div>

<section class="feature-band">
  <div class="feature"><h2>Knowledge Management</h2><p>We here modify the site to improve the ranking by using the keywords and contents.</p><div class="read-more">READ MORE..</div></div>
  <div class="feature"><h2>Continuous Improvement</h2><p>We here modify the site to improve the ranking by using the keywords and contents.</p><div class="read-more">READ MORE..</div></div>
  <div class="feature"><h2>Business Transformation</h2><p>We here modify the site to improve the ranking by using the keywords and contents.</p><div class="read-more">READ MORE..</div></div>
  <div class="feature"><h2>System Requirements</h2><p>We here modify the site to improve the ranking by using the keywords and contents.</p><div class="read-more">READ MORE..</div></div>
</section>

<main class="content">
  <h2>We power and de-risk business transformations</h2>
  <p>Operational excellence and business transformation is achieved by understanding and capturing every detail of your business. High performing companies have a single view of the complex relationships between systems, processes and people supported by in depth organizational knowledge. Vantrelux’s Operational Business Management System (OBMS) empowers and de-risks large transformation initiatives enabling continuous improvement for high performing organizations.</p>
  <p>An OBMS captures the DNA of your business. It links people, processes and systems in a way that visualizes how your organization works today, and how it may change in the future. This information is managed in a re-usable and extendable framework and is distributed to the many stakeholders in a form that meets their individual needs.</p>
  <p>This unique way of reaching, engaging and empowering everyone involved in your business allows you to continually excel in your operations and reduce costs while maintaining compliance and governance standards. Vantrelux’s OBMS allows you to:</p>
  <p>Brightlane Web Studio is a professional website design company dedicated to provide excellent services. We at Brightlane Web Studio think graphic design as a combination and collaboration of ideas and technology. Our Website Design team give an unforgettable impression on the customers and the clients. We can assure you that this is the best place for requirement of yours regarding website design solutions</p>
  <p>Brightlane Web Studio provides you the Search Engine Optimization making your website search engine friendly. So that the website can achieve top position and ranking in the Internet searches and thereby increasing the scope for the website to be found by customers. We here modify the site to improve the ranking by using the keywords and contents</p>
  <ul class="benefits">
    <li>Build a knowledge management system that captures and reuses your expertise.</li>
    <li>Undertake business transformations that reduce risk and cost and increase the benefits.</li>
    <li>Implement continuous improvement as a natural part of your business processes.</li>
    <li>Create business process models that are understood to business users.</li>
    <li>Create systems requirements that relate business processes to IT systems capability.</li>
    <li>Deliver governance and compliance through auditable and traceable operational systems.</li>
  </ul>
</main>

<aside class="sidebar">
  <h3>Latest Video</h3>
  <div class="video">
    <svg width="237" height="148" viewBox="0 0 237 148">
      <polygon points="105,57 105,81 126,69" fill="#fff"/>
      <line x1="20" y1="135" x2="228" y2="135" stroke="#ddd" stroke-width="1.5"/>
      <circle cx="27" cy="135" r="4.5" fill="#fff"/>
    </svg>
  </div>
  <div class="news">
    <h3>News &amp; Events</h3>
    <div class="news-item">
      <svg width="38" height="42" viewBox="0 0 38 42"><rect x="1" y="4" width="36" height="37" rx="3" fill="#f4f4f4" stroke="#333" stroke-width="2"/><rect x="2" y="5" width="34" height="10" fill="#2a7fd0"/><text x="5" y="13" font-size="6" fill="#fff" font-family="Open Sans,sans-serif">SEP</text><text x="19" y="36" font-size="19" font-weight="700" text-anchor="middle" fill="#222" font-family="Open Sans,sans-serif">12</text><rect x="8" y="1" width="3" height="7" fill="#555"/><rect x="27" y="1" width="3" height="7" fill="#555"/></svg>
      <div class="news-body"><div class="news-date">12 Sep 2012</div><div class="news-text">So that the website can achieve top position and ranking in the Internet searches</div><span class="news-more">READ <b>MORE</b></span></div>
    </div>
    <div class="news-item">
      <svg width="38" height="42" viewBox="0 0 38 42"><rect x="1" y="4" width="36" height="37" rx="3" fill="#f4f4f4" stroke="#333" stroke-width="2"/><rect x="2" y="5" width="34" height="10" fill="#2a7fd0"/><text x="5" y="13" font-size="6" fill="#fff" font-family="Open Sans,sans-serif">SEP</text><text x="19" y="36" font-size="19" font-weight="700" text-anchor="middle" fill="#222" font-family="Open Sans,sans-serif">12</text><rect x="8" y="1" width="3" height="7" fill="#555"/><rect x="27" y="1" width="3" height="7" fill="#555"/></svg>
      <div class="news-body"><div class="news-date">12 Sep 2012</div><div class="news-text">So that the website can achieve top position and ranking in the Internet searches</div><span class="news-more">READ <b>MORE</b></span></div>
    </div>
  </div>
</aside>

<footer class="site-footer">
  <div class="footer-col" style="left:20px">
    <h4>PRODUCTS</h4>
    <ul><li>Flowpedia</li><li>Vantrelux Modeler</li><li>System Requirements Modeler</li><li>Performance Improvement Modeler</li><li>Enterprise Architect Modeler</li><li>Corporate Governance Modeler</li></ul>
  </div>
  <div class="footer-col" style="left:220px">
    <h4>SERVICES</h4>
    <ul><li>Coaching &amp; Mentoring</li><li>Technical Services</li></ul>
    <h4 style="margin-top:14px">NEWS &amp; EVENTS</h4>
    <ul><li>Announcements</li><li>Technical Notes</li></ul>
  </div>
  <div class="footer-col" style="left:371px">
    <h4>TRAINING &amp; SUPPORT</h4>
    <ul><li>Text-Based Tutorials</li><li>Tutorial Movies</li><li>Knowledge Base</li><li>Forums</li><li>Training Courses</li></ul>
  </div>
  <div class="footer-col" style="left:549px">
    <h4>CONTACT INFORMATION</h4>
  </div>
</footer>

<div class="footer-bar">
  <span class="copyright">© Copyright VANTRELUX 2012 - All Rights Reserved</span>
  <span class="legal">TERMS &amp; CONDITIONS | PRIVACY POLICY | MAINTENANCE POLICY</span>
</div>
</body>
</html>
```